Yard sign

Looking for a yard sign. <br/>Something simple, name, number. <br/>Large text, readable from 50 feet away. <br/><br/>18 x 24 inches.

Target Market(s)

Potential homeowners thinking about going solar.

Colors

Designer to choose colors to be used in the design.

Requirements
Must have
• "WE'VE GONE SOLAR!"
Nice to have
• We are a solar company, we would like a design that compliments the homeowners decision that they went solar and encourages others to do the same.

```html
<!DOCTYPE html>
<html lang="en">
<head>
<meta charset="UTF-8">
<title>We've Gone Solar – Yard Sign</title>
<link rel="stylesheet" href="https://fonts.googleapis.com/css2?family=Montserrat:wght@300;700;800&display=swap">
<style>
  :root {
    --backdrop: #221f20;
    --sign-base: #2a2929;
    --sign-glow: #474646;
    --solar-gold: #fdb515;
    --sun-orange: #f47a10;
    --band-orange: #e35704;
    --white: #ffffff;
  }
  * { margin: 0; padding: 0; box-sizing: border-box; }
  html, body {
    width: 1200px; height: 1200px; overflow: hidden;
    background: var(--backdrop);
    font-family: "Montserrat", sans-serif;
  }
  .sign {
    position: absolute; left: 48px; top: 163px;
    width: 1104px; height: 827px;
    background: radial-gradient(ellipse 70% 55% at 50% 20%, var(--sign-glow), var(--sign-base) 75%);
  }
  .brand {
    position: absolute; left: 48px; top: 178px;
    width: 440px; height: 150px;
    display: flex; align-items: center; gap: 20px;
  }
  .brand-dot {
    flex: none; width: 86px; height: 86px; border-radius: 50%;
    background: var(--solar-gold);
  }
  .brand-name {
    color: var(--sun-orange); font-weight: 800;
    font-size: 42px; line-height: 1.05; letter-spacing: 0;
    white-space: nowrap;
  }
  .divider {
    position: absolute; left: 526px; top: 156px;
    width: 3px; height: 211px; background: var(--solar-gold);
  }
  .headline {
    position: absolute; left: 568px; top: 170px;
    color: var(--solar-gold); font-weight: 800; line-height: 1;
    white-space: nowrap;
  }
  .headline .line-1 { display: block; font-size: 66px; letter-spacing: 0; }
  .headline .line-2 { display: block; font-size: 118px; letter-spacing: 0; margin-top: -2px; margin-left: -3px; }
  .phone-band {
    position: absolute; left: 0; top: 505px;
    width: 1104px; height: 151px; background: var(--band-orange);
    display: flex; align-items: center; justify-content: center;
  }
  .phone {
    color: var(--white); font-weight: 700; font-size: 146px;
    letter-spacing: -2px; line-height: 1; padding-left: 60px;
    white-space: nowrap;
  }
  .rep {
    position: absolute; left: 0; top: 690px; width: 1104px;
    display: flex; align-items: center; justify-content: center; gap: 30px;
  }
  .rep-rule {
    height: 4px; background: var(--solar-gold);
    clip-path: polygon(0 30%, 100% 0, 100% 100%, 0 70%);
  }
  .rep-rule.left { width: 154px; }
  .rep-rule.right { width: 182px; transform: scaleX(-1); }
  .rep-name {
    color: var(--solar-gold); font-weight: 300; font-size: 51px;
    letter-spacing: 8px; line-height: 1; white-space: nowrap;
  }
</style>
</head>
<body>
  <main class="sign">
    <div class="brand">
      <span class="brand-dot"></span>
      <span class="brand-name">BRIGHTFIELD<br>SOLAR</span>
    </div>
    <div class="divider"></div>
    <h1 class="headline">
      <span class="line-1">WE'VE GONE</span>
      <span class="line-2">SOLAR!</span>
    </h1>
    <div class="phone-band">
      <p class="phone">123 456 7890</p>
    </div>
    <div class="rep">
      <span class="rep-rule left"></span>
      <p class="rep-name">JONATHAN DOE</p>
      <span class="rep-rule right"></span>
    </div>
  </main>
</body>
</html>
```